Moxy Fen needs some awesome stationary

Do you have what it takes to get my brand? You either do or you don't, have a crack at a design and you my just win my business.

I don't want to waste your or my time, so put your creative genius on either a business card or envelope.

I however need a package of stationary that follows the same brand. I will message you to complete the remaining should I like your first submission.

Here is what I need, have a go!

Basically I need the following for my small business based in melbourne.
- Letterhead (printer ready and MS Word)
- Business Card
- Compliments Slip
- Envelope
- Proposal Cover Page (MS Word only)
- Presentation Folder
- Marbled Fox Cards
- Student Name Tent
- Index Cards
- Vell-Ka

I am establishing the brand and it must be modern, professional but also relaxed; that is not formal and not corporate. It represents a company are leaders, but small enough to care and operate like a bunch of friends. We are bringing people and conversations back to business, and turfing out all the bureaucracy and crazy and wasteful procedures. Its about "lets talk and figure it out together and find even better ways".

Target Market(s)

Mainly companies that build software products, but Agile practices are used in many other industries (even graphic design projects)

Industry/Entity Type

Information Technology

Font styles to use
Sans Serif

Colors
3176b5
aaaaaa

Requirements
Must have
• I like curves and circles and not boxes or rectangles.
• I want a colour rich design with my brand colours, but it must be balanced.
• I want more modern than traditional, but simple modern
Should not have
• Not corporate
• Please don't waste my time if your not going to think about it.
• Don't mess with my primary logo
• Don't change my colours
• Don't overlay logo on image

```html
<!DOCTYPE html>
<html lang="en">
<head>
<meta charset="utf-8">
<title>Moxy Fen – Business Card</title>
<link href="https://fonts.googleapis.com/css2?family=Open+Sans:wght@400;600;700&display=swap" rel="stylesheet">
<style>
  :root {
    --brand-blue: #3176b5;
    --deep-blue: #2a5aa6;
    --brand-grey: #aaaaaa;
    --slate: #8b95a7;
    --ink: #3c3f45;
    --muted: #7d8290;
    --paper: #ffffff;
    --backdrop: #eceef1;
  }
  * { box-sizing: border-box; margin: 0; padding: 0; }
  html, body {
    width: 1200px; height: 950px; overflow: hidden;
    background: var(--backdrop);
    font-family: "Open Sans", Arial, sans-serif;
  }
  .stage { position: relative; width: 1200px; height: 950px; }

  /* Front of card */
  .card-front {
    position: absolute; left: 60px; top: 120px;
    width: 620px; height: 360px;
    background: var(--paper);
    border-radius: 26px;
    overflow: hidden;
    box-shadow: 0 6px 18px rgba(0,0,0,.12);
  }
  .front-band { position: absolute; left: 0; bottom: 0; width: 620px; height: 130px; }
  .web-address {
    position: absolute; left: 372px; bottom: 18px;
    color: var(--paper); font-size: 15px; letter-spacing: 1px; line-height: 1;
    white-space: nowrap;
    transform: rotate(-10deg); transform-origin: left bottom;
  }
  .brand-mark {
    position: absolute; left: 48px; top: 118px;
    display: flex; align-items: center; gap: 14px;
  }
  .brand-dot { width: 34px; height: 34px; border-radius: 50%; background: var(--brand-grey); }
  .brand-name { font-size: 42px; font-weight: 700; color: var(--deep-blue); }

  .contact {
    position: absolute; left: 330px; top: 36px;
    padding-left: 26px;
    border-left: 1px solid #d4d7dc;
    height: 196px;
  }
  .person-name { font-size: 22px; font-weight: 700; color: var(--deep-blue); }
  .person-role { font-size: 14px; color: var(--brand-grey); margin-bottom: 12px; }
  .address { font-size: 14px; color: var(--ink); line-height: 1.45; margin-bottom: 8px; }
  .contact-line { display: flex; align-items: center; gap: 10px; font-size: 14px; color: var(--ink); line-height: 1.6; }
  .contact-line svg { width: 14px; height: 14px; fill: var(--deep-blue); flex: none; }

  /* Back of card */
  .card-back {
    position: absolute; left: 740px; top: 230px;
    width: 380px; height: 620px;
    background: var(--slate);
    border-radius: 26px;
    overflow: hidden;
    box-shadow: 0 6px 18px rgba(0,0,0,.12);
  }
  .back-name {
    position: absolute; left: 36px; top: 40px;
    font-size: 48px; font-weight: 700; color: var(--paper);
  }
  .back-web {
    position: absolute; left: 38px; top: 110px;
    font-size: 16px; letter-spacing: 3px; color: var(--paper);
  }
  .back-circle {
    position: absolute; left: 40px; top: 200px;
    width: 300px; height: 300px; border-radius: 50%;
    background: var(--deep-blue);
  }
</style>
</head>
<body>
<main class="stage">

  <section class="card-front" aria-label="Business card front">
    <div class="brand-mark">
      <span class="brand-dot"></span>
      <span class="brand-name">Moxy Fen</span>
    </div>

    <div class="contact">
      <p class="person-name">Dana Kellow</p>
      <p class="person-role">CEO, Professional Agile Trainer</p>
      <p class="address">PO Box 4417<br>Ashgrove Hill<br>VIC 3999, Australia</p>
      <p class="contact-line">
        <svg viewBox="0 0 16 16"><path d="M4 1l3 3-2 2c1 2 3 4 5 5l2-2 3 3-2 3C7 15 1 9 1 3z"/></svg>
        1300 555 019
      </p>
      <p class="contact-line">
        <svg viewBox="0 0 16 16"><path d="M4 0h8a1 1 0 0 1 1 1v14a1 1 0 0 1-1 1H4a1 1 0 0 1-1-1V1a1 1 0 0 1 1-1zm1 2v10h6V2z"/></svg>
        +61 400 555 127
      </p>
      <p class="contact-line">
        <svg viewBox="0 0 16 16"><path d="M1 3h14v10H1zm1 1.5v.3l6 4 6-4v-.3z"/></svg>
        dana@moxyfen.example
      </p>
    </div>

    <svg class="front-band" viewBox="0 0 620 130" preserveAspectRatio="none" aria-hidden="true">
      <path d="M0 92 Q330 70 620 0 L620 130 L0 130 Z" fill="#c9cdd4"/>
      <path d="M0 100 Q330 80 620 12 L620 130 L0 130 Z" fill="var(--deep-blue)"/>
    </svg>
    <p class="web-address">www.moxyfen.example</p>
  </section>

  <section class="card-back" aria-label="Business card back">
    <p class="back-name">Moxy Fen</p>
    <p class="back-web">www.moxyfen.example</p>
    <div class="back-circle"></div>
  </section>

</main>
</body>
</html>
```